Highlight Document Over Image for Slide

We are seeking a graphic designer to overlay a news article on an image that pertains to the article, aiming for a stylish yet professional appearance. Given the limited resources, we encourage you to use your imagination and go beyond what basic tools like PowerPoint can offer.

```html
<!DOCTYPE html>
<html lang="en">
<head>
<meta charset="utf-8">
<title>Introduction or Possession of Contraband Items</title>
<link rel="stylesheet" href="https://fonts.googleapis.com/css2?family=Montserrat:wght@400;700&display=swap">
<style>
  :root {
    --page-bg: #f0f0f0;
    --slide-bg: #f4f5f8;
    --ink: #111111;
    --rule: #555555;
    --card-fill: rgba(255, 255, 255, 0.78);
    --card-border: #222222;
    --pill: #000000;
    --pill-text: #ffffff;
    --terrain-dry: #a88a58;
    --terrain-green: #6f7446;
    --roofs: #8b7f78;
    --water: #6e6e66;
  }
  * { box-sizing: border-box; margin: 0; padding: 0; }
  html, body {
    width: 1200px;
    height: 1200px;
    overflow: hidden;
    background: var(--page-bg);
  }
  .slide {
    position: absolute;
    left: 20px;
    top: 273px;
    width: 1160px;
    height: 654px;
    background: var(--slide-bg);
    overflow: hidden;
  }
  .aerial-view {
    position: absolute;
    inset: 0;
    clip-path: polygon(0 0, 955px 0, 699px 100%, 0 100%);
    background:
      radial-gradient(ellipse 420px 240px at 130px 610px, var(--water) 0%, var(--water) 60%, transparent 62%),
      linear-gradient(160deg, transparent 55%, rgba(110,110,102,0.85) 78%),
      radial-gradient(ellipse 300px 220px at 300px 250px, var(--roofs) 0%, transparent 75%),
      radial-gradient(ellipse 260px 160px at 600px 60px, var(--terrain-green) 0%, transparent 80%),
      linear-gradient(180deg, var(--terrain-dry) 0%, #8f7d63 45%, #7d7468 100%);
  }
  .notice-card {
    position: absolute;
    left: 458px;
    top: 75px;
    width: 624px;
    height: 523px;
    background: var(--card-fill);
    border: 2px solid var(--card-border);
    border-radius: 12px;
    font-family: "Montserrat", sans-serif;
    color: var(--ink);
  }
  .notice-title {
    position: absolute;
    top: 56px;
    left: 0;
    right: 0;
    text-align: center;
    font-weight: 700;
    font-size: 20.5px;
    line-height: 30px;
    letter-spacing: 0.2px;
  }
  .rule {
    position: absolute;
    left: 93px;
    width: 437px;
    height: 1px;
    background: var(--rule);
  }
  .rule-top { top: 132px; }
  .rule-bottom { top: 449px; }
  .notice-body {
    position: absolute;
    top: 142px;
    left: 52px;
    width: 528px;
    font-size: 18.6px;
    line-height: 26.6px;
    text-align: justify;
    font-weight: 400;
    letter-spacing: 0.3px;
  }
  .page-number {
    position: absolute;
    left: 270px;
    top: 465px;
    width: 88px;
    height: 40px;
    border-radius: 20px;
    background: #ffffff;
    padding: 3px;
  }
  .page-number span {
    display: flex;
    align-items: center;
    justify-content: center;
    width: 100%;
    height: 100%;
    border-radius: 17px;
    background: var(--pill);
    color: var(--pill-text);
    font-size: 13px;
    letter-spacing: 4px;
    padding-left: 4px;
  }
</style>
</head>
<body>
  <section class="slide">
    <div class="aerial-view" role="img" aria-label="Aerial satellite view of a waterfront correctional facility with buildings, yards, roads and bay water"></div>
    <article class="notice-card">
      <h1 class="notice-title">INTRODUCTION OR POSSESSION OF<br>CONTRABAND ITEMS</h1>
      <div class="rule rule-top"></div>
      <p class="notice-body">Employees shall not introduce or possess unauthorized items such as escape paraphernalia, weapons, facsimiles of weapons, ammunition, wireless communication devices, cell phones, tobacco or facsimiles of tobaccos products (e.g. electronic vapor cigarettes) lighters or any other item not specifically authorized by PD 04.04.100 “Custody, Security and Safety Systems (Exempt)”, OP 04.04.100 “Gate Security” or facility operating procedure in any facility where offenders are housed. Employees are responsible for any item in their</p>
      <div class="rule rule-bottom"></div>
      <div class="page-number"><span>36</span></div>
    </article>
  </section>
</body>
</html>
```